Fitness Equipment & Service

I want to make the card eye catching and fun. We are called Corvane Motion Limited and we are based in Wales. We sell, install and service all types of fitness equipment from Skipping ropes, right through the Dumbbells, Kettle bells and Barbells through to state of the art Treadmills, Running Machines and Strength Equipment. We also design and install changing room furniture and lockers.

TYPOGRAPHY
We would like to use Futrura. Futura has an appearance of efficiency and forwardness. The typeface is derived
from simple geometric forms (near-perfect circles, triangles and squares) and is based on strokes of
near-even weight, which are low in contrast. This is most visible in the almost perfectly round stroke of
the o, which is nonetheless slightly ovoid.
The lowercase has tall ascenders, which rise above the cap line. The uppercase
characters present proportions similar to those of classical Roman capitals.

TYPOGRAPHIC CONSIDERATIONS
No Strike though
No Horizontal Scaling
No Drop Shadows
No Effects
Never use less than 120% Leading

OUR CORPORATE COLOURS
BRAND GUIDELINES
We were thinking that our primary colour palette consists of the Acid Green (Pantone 382) and Process Black.

We work closely with tquarly Ltd and would like to include their name on the card somewhere. I have attached images of the other brands that we work with as an idea or the small icons I have included that illustrate what we do?. I have very kindly been given permission to use any of the images off the files that I have included below, so I hope these help. I will include these below. I would be open to suggestions if it made the card more striking Can you do it?
Updates

Hi All, Just wanted to add a few thoughts but you are the guys with the creative visions (thats why are here) We are based in Wales, UK and we would be open to lots of different ideas on a theme but must be eye catching, Bold and FUN. If you can or think that the Welsh or any dragon could be put in there then go for it (its not a must have) We have also added some ideas for colour but again its over to you!! GO FOR IT ! Thanks and look forward to your visions! Owen

Hi All, Just thought I would sen through the contact details that need to be on the card. (if you want to play around with icons instead of the wording twitter, Facebook, go for it): Corvane Motion Limited Owen Pritchard Managing Director Mob: +44 (0)7582 913 406 e-mail: sales@corvanemotion.co.uk Web: Corvanemotion.co.uk twitter: @motionLetterbin Facebook: Corvane Motion Limited

```html
<!DOCTYPE html>
<html lang="en">
<head>
<meta charset="utf-8">
<title>Corvane Motion Limited – Business Card</title>
<link href="https://fonts.googleapis.com/css2?family=Jost:wght@400;500;700&family=Libre+Baskerville:wght@700&display=swap" rel="stylesheet">
<style>
  :root {
    --stage: #e9e6e1;
    --card-black: #0c0c0e;
    --card-white: #f7f7f8;
    --gold: #d6b24a;
    --navy: #26296b;
    --ink: #1a1a1f;
    --blue-deep: #0f3d7a;
    --blue-mid: #1f6fb8;
    --blue-bright: #3aa3e3;
    --white: #ffffff;
  }
  * { box-sizing: border-box; margin: 0; padding: 0; }
  html, body {
    width: 1200px; height: 892px; overflow: hidden;
    background: var(--stage);
  }
  .canvas {
    position: relative; width: 1200px; height: 892px;
    display: flex; align-items: center; justify-content: center; gap: 30px;
  }
  .card {
    position: relative; width: 560px; height: 320px; overflow: hidden;
    border-radius: 4px;
    box-shadow: 0 6px 18px rgba(0,0,0,.18);
  }

  /* Front */
  .card-front { background: var(--card-white); }
  .front-shape { position: absolute; inset: 0; }
  .holder { position: absolute; top: 8px; right: 60px; text-align: left; }
  .holder-name {
    font-family: "Libre Baskerville", serif; font-weight: 700;
    font-size: 28px; line-height: 1.2; color: var(--gold);
  }
  .holder-role {
    font-family: "Jost", sans-serif; font-weight: 400;
    font-size: 18px; line-height: 1.2; color: var(--white);
    margin-left: 38px;
  }
  .brand-mark {
    position: absolute; left: 48px; top: 110px;
    width: 110px; height: 110px; border-radius: 50%;
    background: var(--navy); border: 4px solid #c9ccd6;
  }
  .brand-name {
    position: absolute; left: 240px; bottom: 24px; width: 200px;
    font-family: "Jost", sans-serif; font-weight: 500;
    font-size: 17px; line-height: 1.2; color: var(--navy);
    text-transform: uppercase; letter-spacing: .04em;
  }
  .contacts {
    position: absolute; right: 16px; top: 118px;
    list-style: none; text-align: right;
  }
  .contacts li {
    display: flex; justify-content: flex-end; align-items: center; gap: 8px;
    font-family: "Jost", sans-serif; font-weight: 400;
    font-size: 15px; line-height: 1.5; color: var(--ink);
  }
  .contact-icon {
    width: 14px; height: 14px; background: var(--navy); border-radius: 2px;
    display: inline-flex; align-items: center; justify-content: center; flex: none;
  }
  .contact-icon svg { width: 10px; height: 10px; }

  /* Back */
  .card-back { background: var(--blue-deep); }
  .back-grid {
    position: absolute; inset: 0;
    display: grid; grid-template-columns: repeat(5, 1fr); grid-template-rows: repeat(3, 1fr);
  }
  .tile { background: var(--blue-mid); }
  .tile.dark { background: var(--blue-deep); }
  .tile.bright { background: var(--blue-bright); }
  .plate-image {
    position: absolute; right: -60px; top: -40px; width: 300px; height: 300px; border-radius: 50%;
    background: radial-gradient(circle, #0b1f3d 0 30%, #174a86 31% 60%, rgba(10,30,60,.6) 61% 100%);
    opacity: .75;
  }
  .equipment-icons { position: absolute; inset: 0; }
  .equipment-icons span {
    position: absolute; width: 54px; height: 48px; border-radius: 6px;
    background: rgba(255,255,255,.85);
  }
  .back-name {
    position: absolute; left: 0; right: 0; top: 128px; text-align: center;
    font-family: "Jost", sans-serif; font-weight: 700;
    font-size: 50px; line-height: 1.2; color: var(--white);
    letter-spacing: .02em;
  }
</style>
</head>
<body>
<main class="canvas">

  <section class="card card-front" aria-label="Card front">
    <svg class="front-shape" viewBox="0 0 560 320" preserveAspectRatio="none" aria-hidden="true">
      <path d="M0 0 H560 V86 C474 90 398 104 350 134 C310 160 272 238 164 320 H0 Z" fill="var(--gold)"/>
      <path d="M0 0 H560 V74 C470 78 390 92 340 124 C300 150 260 230 150 320 H0 Z" fill="var(--card-black)"/>
    </svg>

    <div class="holder">
      <p class="holder-name">Owen Pritchard</p>
      <p class="holder-role">Managing Director</p>
    </div>

    <div class="brand-mark" aria-hidden="true"></div>
    <p class="brand-name">Corvane Motion Limited</p>

    <ul class="contacts">
      <li>+44 (0)7582 913 406
        <span class="contact-icon"><svg viewBox="0 0 10 10"><path d="M2 1 L4 1 L4.6 3 L3.6 3.8 C4 5 5 6 6.2 6.4 L7 5.4 L9 6 L9 8 C5 9 1 5 2 1 Z" fill="#fff"/></svg></span>
      </li>
      <li>sales@corvanemotion.co.uk
        <span class="contact-icon"><svg viewBox="0 0 10 10"><rect x="1" y="2.5" width="8" height="5" fill="none" stroke="#fff" stroke-width="1"/><path d="M1 2.5 L5 5.5 L9 2.5" fill="none" stroke="#fff" stroke-width="1"/></svg></span>
      </li>
      <li>Corvanemotion.co.uk
        <span class="contact-icon"><svg viewBox="0 0 10 10"><circle cx="5" cy="5" r="3.5" fill="none" stroke="#fff" stroke-width="1"/></svg></span>
      </li>
      <li>Corvane Motion Limited
        <span class="contact-icon"></span>
      </li>
      <li>@motionLetterbin
        <span class="contact-icon"></span>
      </li>
    </ul>
  </section>

  <section class="card card-back" aria-label="Card back">
    <div class="back-grid" aria-hidden="true">
      <div class="tile dark"></div><div class="tile"></div><div class="tile bright"></div><div class="tile dark"></div><div class="tile"></div>
      <div class="tile"></div><div class="tile dark"></div><div class="tile"></div><div class="tile bright"></div><div class="tile dark"></div>
      <div class="tile bright"></div><div class="tile"></div><div class="tile dark"></div><div class="tile"></div><div class="tile bright"></div>
    </div>
    <div class="plate-image" role="img" aria-label="Photograph of a weight plate in deep blue tones"></div>
    <div class="equipment-icons" role="img" aria-label="Small illustrations of fitness equipment: nutrition, lockers, rowing machine, boxing gloves and skipping rope">
      <span style="left:22px; top:28px"></span>
      <span style="left:140px; top:28px"></span>
      <span style="left:22px; top:240px"></span>
      <span style="left:372px; top:240px"></span>
      <span style="left:484px; top:240px"></span>
    </div>
    <p class="back-name">Corvane Motion</p>
  </section>

</main>
</body>
</html>
```